QHX Compliant Dietary Supplement Label for Nutritional Company

We are in need of a label for our line of 20+ dietary supplements that are specifically formulated to balance body chemistry and match the biochemical individuality of our users based on hair tissue mineral analysis.

We have a line of approximately 20 different dietary supplements that will require use of new label in both a small (90 capsule) and large (180 capsule) size. We will start with the initial label in which Product name, Supplement Facts, and Ingredient list will need to be modified for each particular product thereafter.

The label will be placed on a transparent blue bottle with the color of lid being decided after label design. We are open to a transparent light amber bottle with black lid but blue is our preference.

We would like the majority of the label to be blue. Solid blue, fading of blue to darker blue/black, or subtle background designs are welcome with involvement of white and hints of orange. We do not want pictorial images on the label.

Label size:
Small bottle (120cc): Label size ~ 2.25” x 5.875”
Large bottle (200cc): Label size ~ 2.75” x 7.625”

Front:
-Logo near top of label with product name and description in middle and capsule count near the bottom

Right Side:
-Supplement Facts: See current product image below in brief
-Ingredient list: See current product image below in brief
-Manufactured for: See image below (This is on the left side of our current bottle and would like it moved to the bottom of the right side)

Left side:
-Suggested use: See current product image below in brief
-Leave room for possible warning statement
-Leave room for possible lot number printing
-Keep out of the reach of children.

The first files below are our current supplement label with product information. This information is what is needed on the label and will likely need some adjustments as we are updating our line of supplements and changes in QHX requirements.

The following files are the logo files and color palette.

The remaining files are some designs we came across for inspiration.

Thank you.

Target Market(s)

Health Care Profressionals

Industry/Entity Type

Health Care and Nutrition

Requirements
Nice to have
• Product name needs to be on same line in all one color
Should not have
• Pictorial Images

```html
<!DOCTYPE html>
<html lang="en">
<head>
<meta charset="utf-8">
<title>ARVO-LENE Adrenal Supplement Label</title>
<link href="https://fonts.googleapis.com/css2?family=Montserrat:wght@400;500;700&display=swap" rel="stylesheet">
<style>
  :root {
    --page-bg: #f4f4f4;
    --label-blue: #2b3253;
    --label-blue-edge: #3d4465;
    --accent-orange: #f08a41;
    --ink-white: #fafafa;
    --ink-navy: #2b3253;
  }
  html, body {
    margin: 0;
    padding: 0;
    width: 1200px;
    height: 960px;
    overflow: hidden;
    background: var(--page-bg);
    font-family: "Montserrat", sans-serif;
  }
  .front-label {
    position: absolute;
    left: 278px;
    top: 80px;
    width: 644px;
    height: 800px;
    background: linear-gradient(90deg, var(--label-blue-edge) 0%, var(--label-blue) 20%, var(--label-blue) 80%, var(--label-blue-edge) 100%);
    color: var(--ink-white);
    overflow: hidden;
  }
  .brand-name {
    position: absolute;
    left: 0;
    right: 0;
    top: 128px;
    height: 48px;
    text-align: center;
    font-size: 44px;
    font-weight: 500;
    line-height: 48px;
    letter-spacing: 1px;
  }
  .brand-sub {
    position: absolute;
    left: 0;
    right: 0;
    top: 180px;
    height: 18px;
    text-align: center;
    font-size: 15px;
    font-weight: 500;
    line-height: 18px;
    letter-spacing: 6px;
  }
  .product-word {
    position: absolute;
    left: 0;
    right: 0;
    height: 160px;
    overflow: hidden;
    text-align: center;
    font-size: 181px;
    font-weight: 400;
    line-height: 160px;
    letter-spacing: -2px;
  }
  .product-word--top { top: 244px; }
  .product-word--bottom { top: 428px; }
  .product-dash {
    position: absolute;
    left: 286px;
    top: 409px;
    width: 77px;
    height: 15px;
    background: var(--accent-orange);
  }
  .product-description {
    position: absolute;
    left: 58px;
    top: 607px;
    width: 522px;
    height: 41px;
    background: var(--accent-orange);
    color: var(--ink-navy);
    display: flex;
    align-items: center;
    justify-content: center;
    font-size: 32px;
    font-weight: 700;
    letter-spacing: 1px;
  }
  .capsule-count {
    position: absolute;
    left: 0;
    right: 0;
    top: 707px;
    height: 36px;
    text-align: center;
    font-size: 31px;
    font-weight: 700;
    line-height: 36px;
  }
  .capsule-count .count-number { color: var(--accent-orange); }
</style>
</head>
<body>
  <main class="front-label">
    <div class="brand-name">VELMARA</div>
    <div class="brand-sub">LABORATORIES</div>
    <div class="product-word product-word--top">ARVO</div>
    <div class="product-dash"></div>
    <div class="product-word product-word--bottom">LENE</div>
    <div class="product-description">ADRENAL SUPPLEMENT</div>
    <div class="capsule-count"><span class="count-number">90</span> CAPSULES</div>
  </main>
</body>
</html>
```